Quiet Harbor Prints gallery website

I need a Website for a gallery with a shopify integration or maybe even better also compatible with squarespace.
the website should have following riders: Künstler, Veranstaltungen, Shop, About Us.
some nice examples for inspiration of the website architecture are:
https://www.lindwerkraum.com/
https://www.plattenbau-salon.com/de/
https://moorlichtraum.de/
It should be easy for us to make adaptations and fill the website with new content.
Attached there is the CI an logo for the brand.
Target Market(s)
Art Collectors,
Industry/Entity Type
artgallery
Coding
Coded - Design and coding required
Number of Pages Required
3 page
Font styles to use
Look and feel

```html
<!DOCTYPE html>
<html lang="en">
<head>
<meta charset="utf-8">
<title>Quiet Harbor Prints</title>
<link rel="stylesheet" href="https://fonts.googleapis.com/css2?family=Bellefair&family=DM+Sans:wght@400;700&display=swap">
<style>
  :root {
    --ink: #000000;
    --paper: #ffffff;
    --accent: #c0202a;
    --muted: #8a8a8a;
    --soft: #b4b4b4;
    --rule: #1c1c1c;
  }
  * { box-sizing: border-box; margin: 0; padding: 0; }
  html, body { width: 867px; height: 1200px; overflow: hidden; background: var(--ink); }
  .page { position: relative; width: 867px; height: 1200px; background: var(--ink); color: var(--paper); font-family: "Bellefair", serif; }
  .abs { position: absolute; }

  .brand { left: 26px; top: 50px; width: 102px; text-align: center; }
  .brand-name { font-size: 11px; letter-spacing: 0.3px; color: #d8d8d8; line-height: 1; white-space: nowrap; }

  .nav { top: 42px; font-size: 14px; line-height: 1; }
  .nav a { color: var(--paper); text-decoration: none; position: absolute; white-space: nowrap; }
  .nav a.active { color: var(--accent); }
  .signin { left: 757px; top: 42px; display: flex; align-items: center; gap: 6px; font-size: 14px; line-height: 1; }

  .hero { left: 0; top: 90px; width: 867px; height: 388px;
    background: radial-gradient(ellipse at 50% 45%, #3a3a3a 0%, #242424 45%, #121212 100%); }
  .hero-title { left: 0; top: 214px; width: 867px; text-align: center; font-size: 40px; line-height: 36px; font-weight: 400; }
  .hero-text { left: 225px; top: 310px; width: 417px; text-align: center; font-family: "DM Sans", sans-serif; font-size: 10.5px; line-height: 14px; color: var(--muted); }

  .btn { display: flex; align-items: center; justify-content: center; gap: 22px; background: var(--accent); color: var(--paper); font-family: "DM Sans", sans-serif; font-weight: 700; font-size: 11px; letter-spacing: 0.2px; }
  .btn-shop { left: 371px; top: 361px; width: 124px; height: 30px; }
  .btn-artist { left: 70px; top: 741px; width: 124px; height: 30px; }

  .spot-photo { left: 438px; top: 495px; width: 429px; height: 349px;
    background: linear-gradient(135deg, #2fb7c4 0%, #e0462f 35%, #d9b21a 55%, #1f1f1f 75%, #48c6cf 100%); }
  .spot-title { left: 70px; top: 592px; width: 310px; font-size: 27px; line-height: 31px; font-weight: 400; }
  .spot-text { left: 70px; top: 666px; width: 295px; font-family: "DM Sans", sans-serif; font-size: 11px; line-height: 14px; color: var(--muted); }

  .sub-title { left: 0; top: 908px; width: 867px; text-align: center; font-size: 28px; line-height: 1; font-weight: 400; }
  .sub-text { left: 0; top: 953px; width: 867px; text-align: center; font-size: 10px; color: var(--muted); line-height: 1; }
  .sub-input { left: 324px; top: 986px; width: 154px; height: 22px; border: 1px solid #cfcfcf; border-radius: 2px; display: flex; align-items: center; justify-content: space-between; padding: 0 7px; font-size: 7.5px; color: var(--muted); }
  .sub-input i { width: 7px; height: 5px; background: #555; display: block; }
  .sub-btn { left: 487px; top: 986px; width: 55px; height: 22px; background: var(--accent); display: flex; align-items: center; justify-content: center; font-size: 7.5px; }
  .sub-note { left: 0; top: 1025px; width: 867px; text-align: center; font-size: 8px; line-height: 1; }

  .footer-rule { left: 0; top: 1078px; width: 867px; height: 1px; background: var(--rule); }
  .footer-col { top: 1097px; list-style: none; font-size: 10px; line-height: 16.3px; }
  .footer-brand { left: 353px; top: 1148px; width: 160px; text-align: center; }
  .footer-brand .brand-name { font-size: 13px; }
  .social { left: 676px; top: 1097px; display: flex; gap: 10px; }
  .social span { width: 7px; height: 7px; border-radius: 50%; background: var(--paper); display: block; }
  .lang { left: 670px; top: 1157px; font-size: 10px; color: var(--muted); line-height: 1; }
</style>
</head>
<body>
<div class="page">
  <header>
    <div class="abs brand">
      <div class="brand-name">QUIET HARBOR PRINTS</div>
    </div>
    <nav class="abs nav" style="left:0;width:867px;">
      <a class="active" style="left:302px">Home</a>
      <a style="left:368px">Events</a>
      <a style="left:437px">Gallery</a>
      <a style="left:507px">Shop</a>
      <a style="left:567px">Contact</a>
    </nav>
    <div class="abs signin">
      <svg width="11" height="11" viewBox="0 0 11 11" aria-hidden="true"><circle cx="4.3" cy="4.3" r="3.3" fill="none" stroke="#fff" stroke-width="1.2"/><line x1="6.8" y1="6.8" x2="10.3" y2="10.3" stroke="#fff" stroke-width="1.3"/></svg>
      <span>Sign in</span>
    </div>
  </header>

  <section>
    <div class="abs hero" role="img" aria-label="Dim gallery room with framed black and white photographs on the walls"></div>
    <h1 class="abs hero-title">Discover Fine Art Masterpieces at<br>Quiet Harbor Prints Gallery</h1>
    <p class="abs hero-text">Embark on a journey through timeless beauty and artistic excellence at Quiet Harbor Prints Gallery. Explore our curated collection of exquisite masterpieces.</p>
    <a class="abs btn btn-shop">SHOP
      <svg width="28" height="8" viewBox="0 0 28 8" aria-hidden="true"><line x1="0" y1="4" x2="27" y2="4" stroke="#fff" stroke-width="1"/><polyline points="23,1 27,4 23,7" fill="none" stroke="#fff" stroke-width="1"/></svg>
    </a>
  </section>

  <section>
    <h2 class="abs spot-title">Artist Spotlight: Delving into the Creative Journey</h2>
    <p class="abs spot-text">Dive into the captivating narratives and creative inspirations behind our featured artists. Learn about their unique styles, passions, and contributions to the world of fine art.</p>
    <a class="abs btn btn-artist">ARTIST
      <svg width="28" height="8" viewBox="0 0 28 8" aria-hidden="true"><line x1="0" y1="4" x2="27" y2="4" stroke="#fff" stroke-width="1"/><polyline points="23,1 27,4 23,7" fill="none" stroke="#fff" stroke-width="1"/></svg>
    </a>
    <div class="abs spot-photo" role="img" aria-label="Street artist painting a canvas in front of a colourful graffiti wall"></div>
  </section>

  <section>
    <h2 class="abs sub-title">Subscribe Now</h2>
    <p class="abs sub-text">Nowadays, it isn’t uncommon to see artists rapidly</p>
    <div class="abs sub-input"><span>Enter your email</span><i></i></div>
    <div class="abs sub-btn">Subscribe</div>
    <p class="abs sub-note">We will never spam to you. Only useful info</p>
  </section>

  <footer>
    <div class="abs footer-rule"></div>
    <ul class="abs footer-col" style="left:117px"><li>useful links</li><li>shop</li><li>affiliates</li><li>returns</li></ul>
    <ul class="abs footer-col" style="left:225px"><li>Conditions</li><li>Privacy Policy</li><li>About Us</li><li>Contact</li></ul>
    <div class="abs footer-brand">
      <div class="brand-name">QUIET HARBOR PRINTS</div>
    </div>
    <div class="abs social" aria-label="Social links"><span></span><span></span><span></span><span></span></div>
    <div class="abs lang">English/ German</div>
  </footer>
</div>
</body>
</html>
```